BRIGHTLINE BUILDERS, INC. ELECTRICAL SERVICE

We need a tri-fold pamphlet design for electrical service based in NW Arkansas. We offer Commercial and Industrial Electrical Services including: Infrared imaging, Data Cable Testing, Fiber Optics Testing & Repair, Utility Locates, Preventative Maintenance, Lighting Inspections, Electrical Equipment Cleaning, Automatic Transfer Switch Testing, LED Upgrades with Energy Savings Report.

```html
<!DOCTYPE html>
<html lang="en">
<head>
<meta charset="utf-8">
<title>Brightline Builders, Inc. – Tri-fold Brochure</title>
<link href="https://fonts.googleapis.com/css2?family=Open+Sans:ital,wght@0,400;0,600;0,700;0,800;1,700&family=Tinos:wght@400;700&family=Roboto+Condensed:wght@400;700&display=swap" rel="stylesheet">
<style>
:root{
  --backdrop:#a77c53;
  --blue:#2a46a2;
  --blue-dark:#1f3685;
  --blue-text:#2443a3;
  --ink:#222;
  --grey-light:#e9e9ec;
  --grey-head:#dcdcde;
  --panel:#f2f2f4;
  --white:#fff;
}
*{box-sizing:border-box;margin:0;padding:0}
html,body{width:867px;height:1200px;overflow:hidden}
body{background:var(--backdrop);font-family:"Open Sans",Arial,sans-serif;color:var(--ink);position:relative}
.side-label{position:absolute;left:0;width:867px;text-align:center;color:var(--white);font-weight:700;font-size:26px;letter-spacing:1px}
.sheet{position:absolute;left:101px;width:695px;box-shadow:0 8px 10px rgba(0,0,0,.35)}
.sheet-front{top:83px;height:491px}
.sheet-back{top:612px;height:490px}
.panel{position:absolute;top:0;width:232px;height:476px;overflow:hidden}
.p1{left:0}.p2{left:232px}.p3{left:464px;width:231px}
.base-band{position:absolute;left:0;bottom:0;width:695px;height:15px;background:linear-gradient(90deg,#2b3f8c,#c9ccd8 50%,#2b3f8c)}
.abs{position:absolute}
.head-bar{position:absolute;left:0;top:0;width:100%;height:35px;display:flex;align-items:center;justify-content:center;font-size:14px;color:var(--white);background:var(--blue)}
.head-bar.light{background:var(--grey-head);color:var(--ink);font-weight:700;justify-content:flex-start;padding-left:16px;letter-spacing:.4px}
.head-bar.web{font-weight:700;letter-spacing:.4px}
.photo{position:absolute}
.ticks{list-style:none}
.ticks li{position:relative;padding-left:12px}
.ticks li svg{position:absolute;left:0;top:2px;width:8px;height:8px}
.blue-panel{background:var(--blue);color:var(--white)}
.services-title{left:16px;top:50px;font-size:14px;font-weight:700;letter-spacing:.3px}
.services-list{left:16px;top:76px;font-size:7.5px;font-weight:600;line-height:14.9px}
.about-box{left:19px;top:233px;width:199px;height:243px;background:var(--grey-light);color:var(--ink)}
.about-box h2{text-align:center;font-size:14px;letter-spacing:1px;margin-top:10px;font-weight:700}
.about-box p{font-family:"Tinos","Times New Roman",serif;font-size:7.4px;line-height:10.7px;text-align:justify;text-align-last:center;padding:6px 10px 0}
.serif-title{font-family:"Tinos","Times New Roman",serif;color:var(--blue-text);white-space:nowrap}
.concept{background:var(--panel)}
.concept h2{position:absolute;top:212px;width:100%;text-align:center;font-size:14.5px;font-weight:700}
.concept p{position:absolute;top:238px;left:12px;right:12px;text-align:center;font-family:"Tinos","Times New Roman",serif;font-size:7.2px;line-height:10.7px}
.brand{display:flex;align-items:center;gap:6px;color:var(--blue-text);font-weight:800;letter-spacing:.3px;white-space:nowrap}
.brand i{display:block;background:var(--blue-text)}
.contact-box{left:15px;top:414px;width:201px;height:62px;background:var(--blue-dark);border-radius:5px 5px 0 0;color:var(--white);text-align:center;font-size:7.8px;line-height:12.5px;padding-top:5px}
.contact-box b{font-weight:700}
.hero-type{text-align:center;width:100%;font-weight:700}
.hero-type .big{font-size:14px;line-height:17.5px;color:#111;white-space:nowrap}
.hero-type .elec{font-size:17px;color:var(--blue-text);letter-spacing:.3px;margin:7px auto 0;width:200px;border-top:1px solid #c9c9cf;border-bottom:1px solid #c9c9cf;padding:4px 0 6px;white-space:nowrap}
.hero-type .gen{font-size:14.3px;line-height:18px;color:#111;margin-top:6px}
.white{background:var(--white)}
.body-copy{font-size:7.6px;line-height:11.5px;text-align:justify}
.back-list{font-size:7.5px;line-height:10.8px}
.back-list li{margin-bottom:3.9px}
.other-work{left:21px;top:413px;width:198px;height:62px;display:flex;border-radius:0 5px 5px 0;overflow:hidden}
.other-work .tag{width:48px;background:#8c8c92;color:var(--white);font-family:"Roboto Condensed",Arial,sans-serif;font-size:15px;line-height:17px;text-align:center;display:flex;align-items:center;justify-content:center}
.other-work .list{flex:1;background:var(--blue-dark);color:var(--white);font-style:italic;font-weight:700;font-size:7.3px;line-height:11.7px;padding:5px 8px}
.gen-panel{background:var(--panel)}
.gen-panel h2{position:absolute;top:160px;left:13px;font-size:16.5px;font-weight:400;letter-spacing:1.5px}
.trained{left:13px;top:191px;width:198px;height:52px;background:var(--blue-dark);border-radius:5px;color:var(--white);font-weight:700;font-size:10px;line-height:14px;text-align:center;padding-top:5px}
</style>
</head>
<body>

<svg width="0" height="0" style="position:absolute">
  <defs>
    <symbol id="tick" viewBox="0 0 10 10"><circle cx="5" cy="5" r="5" fill="currentColor"/><path d="M2.6 5.2 4.3 6.9 7.5 3.5" stroke="#2a46a2" stroke-width="1.5" fill="none"/></symbol>
    <symbol id="tick-blue" viewBox="0 0 10 10"><circle cx="5" cy="5" r="5" fill="#2a46a2"/><path d="M2.6 5.2 4.3 6.9 7.5 3.5" stroke="#fff" stroke-width="1.5" fill="none"/></symbol>
  </defs>
</svg>

<div class="side-label" style="top:30px">Side 1</div>

<section class="sheet sheet-front">
  <!-- Panel: services & about -->
  <div class="panel p1 blue-panel">
    <div class="head-bar light">www.brightlinebuilders.net</div>
    <h2 class="abs services-title">SERVICES INCLUDING</h2>
    <ul class="abs ticks services-list" style="color:#fff">
      <li><svg><use href="#tick"/></svg>INFRARED IMAGING,</li>
      <li><svg><use href="#tick"/></svg>DATA CABLE TESTING,</li>
      <li><svg><use href="#tick"/></svg>FIBER OPTICS TESTING &amp; REPAIR,</li>
      <li><svg><use href="#tick"/></svg>UTILITY LOCATES,</li>
      <li><svg><use href="#tick"/></svg>PREVENTATIVE MAINTENANCE,</li>
      <li><svg><use href="#tick"/></svg>LIGHTING INSPECTIONS,</li>
      <li><svg><use href="#tick"/></svg>ELECTRICAL EQUIPMENT CLEANING,</li>
      <li><svg><use href="#tick"/></svg>AUTOMATIC TRANSFER SWITCH TESTING,</li>
      <li><svg><use href="#tick"/></svg>LED UPGRADES WITH ENERGY SAVINGS REPORT</li>
    </ul>
    <div class="abs about-box">
      <h2>ABOUT US</h2>
      <p>Since 1972, Brightline has been serving Northwest Arkansas. As our customers needed more services, we expanded our workforce, our equipment, our technology, and our capacity to meet those needs. Today, we provide complete contracting and engineering services for clients across the nation and around the world.</p>
      <div class="photo" role="img" aria-label="Photo of company awards and plaques on a table" style="left:20px;top:116px;width:155px;height:117px;background:linear-gradient(160deg,#8b5a3c,#5c3220 60%,#3a1f14)"></div>
    </div>
  </div>

  <!-- Panel: concept & contact -->
  <div class="panel p2 concept">
    <div class="head-bar">Call Us:&nbsp;<b>479.555.0142</b></div>
    <div class="photo" role="img" aria-label="Photo of an industrial training facility with overhead lights" style="left:0;top:35px;width:232px;height:191px;background:linear-gradient(180deg,#e8e8ea,#cfd0d4 45%,#a8543f 80%,#c9c9cc)"></div>
    <h2 class="serif-title">From concept to completion</h2>
    <p>Brightline's diversified workforce is comprised of over 600 expert craftspeople; with an offering of mechanical, electrical contracting and specialized services, we provide a 360-degree approach for comprehensive contracting solutions.</p>
    <div class="abs brand" style="left:36px;top:350px;font-size:10px"><i style="width:14px;height:14px"></i>BRIGHTLINE BUILDERS, INC.</div>
    <div class="abs contact-box">
      1450 North Ridge Road, P.O. Box 880<br>
      Springdale, AR 72700-0880<br>
      <b>Phone:</b> 479.555.0142<br>
      <b>Toll-Free:</b> 800.555.0199
    </div>
  </div>

  <!-- Panel: cover -->
  <div class="panel p3 white">
    <div class="head-bar web">www.brightlinebuilders.net</div>
    <div class="photo" role="img" aria-label="Photo of a hand gripping a bolt of electricity" style="left:0;top:35px;width:231px;height:191px;background:radial-gradient(circle at 55% 45%,#bfe3ff 0,#3d7fc4 25%,#13264d 60%,#0b1428)"></div>
    <div class="abs hero-type" style="top:238px">
      <div class="big">RESIDENTIAL AND<br>COMMERCIAL/INDUSTRIAL</div>
      <div class="elec">ELECTRICAL SERVICE</div>
      <div class="gen">GENERATOR SALES<br>AND SERVICE</div>
    </div>
    <div class="abs brand" style="left:28px;top:420px;font-size:11px"><i style="width:16px;height:16px"></i>BRIGHTLINE BUILDERS, INC.</div>
  </div>
  <div class="base-band"></div>
</section>

<section class="sheet sheet-back">
  <!-- Panel: electrical contractors -->
  <div class="panel p1 white">
    <h2 class="abs serif-title" style="left:20px;top:22px;font-size:13.5px;font-weight:700">Division 12 Electrical Contractors</h2>
    <div class="abs body-copy" style="left:20px;top:48px;width:202px">
      <p>From design-build and project management services to complete new-construction services, implementation, and maintenance, Brightline is ready to meet your needs in electrical engineering and contracting.</p>
      <p style="margin-top:5px">Brightline can provide full MEP services, or we can step in when you need specialized services.</p>
    </div>
    <h2 class="abs serif-title" style="left:20px;top:152px;font-size:13.5px;font-weight:700">24-Hour Service 7 Days a Week</h2>
    <ul class="abs ticks back-list" style="left:20px;top:176px;width:202px">
      <li><svg><use href="#tick-blue"/></svg>Complete commercial, industrial and institutional services</li>
      <li><svg><use href="#tick-blue"/></svg>Service and updating of electrical systems and substations</li>
      <li><svg><use href="#tick-blue"/></svg>Design-build capabilities with licensed engineers on staff</li>
      <li><svg><use href="#tick-blue"/></svg>Qualified personnel to service the industrial needs from repairs and retrofits to complete systems</li>
      <li><svg><use href="#tick-blue"/></svg>A staff of full-time estimators to ensure timely turnaround project quotes</li>
      <li><svg><use href="#tick-blue"/></svg>Installation, replacement and repair of poles, lighting and transformers</li>
      <li><svg><use href="#tick-blue"/></svg>Lineman, bucket truck, commercial pole setting equipment</li>
      <li><svg><use href="#tick-blue"/></svg>Thermography</li>
    </ul>
    <div class="abs other-work">
      <div class="tag">OTHER<br>WORK<br>AREA</div>
      <div class="list">HVACR, Generators, Automation + Robotics, Electrical, Mechanical/ Plumbing, Fabrication/Millwright, Cranes + Rigging, Sheet Metal</div>
    </div>
  </div>

  <!-- Panel: generators -->
  <div class="panel p2 gen-panel">
    <div class="photo" role="img" aria-label="Photo of a lineman in a bucket truck at a utility pole" style="left:0;top:0;width:118px;height:148px;background:linear-gradient(180deg,#5f8fd0,#9cc0ea 60%,#cfd9e6)"></div>
    <div class="photo" role="img" aria-label="Photo of an open electrical control panel" style="left:118px;top:0;width:114px;height:148px;background:linear-gradient(180deg,#6f7379,#b9bcc0 40%,#8a8d92)"></div>
    <h2 class="serif-title">GENERATORS</h2>
    <div class="abs body-copy" style="left:13px;top:187px;width:206px">
      <p>Emergency generators start and run automatically when you have a power outage. That means peace of mind, whether you're ensuring that your inventory maintains the required storage temperature or keeping your family comfortable.</p>
      <p style="margin-top:10px">Brightline Builders is now offering service for emergency or backup generators for residential and light commercial applications. You can come to us for sales, installation, and service of emergency generators for home or business.</p>
      <p style="margin-top:10px;text-align:left">Choose Brightline for the top brands of generators, including Voltmax and Powerline. Then stick with us for installation and service in the years to come.</p>
    </div>
    <ul class="abs ticks" style="left:13px;top:368px;font-size:7.5px;line-height:14px">
      <li><svg><use href="#tick-blue"/></svg>Service 24/7, 365 days a year</li>
      <li><svg><use href="#tick-blue"/></svg>Factory trained technicians</li>
      <li><svg><use href="#tick-blue"/></svg>Fully equipped service vehicles</li>
      <li><svg><use href="#tick-blue"/></svg>Complete inventory to handle all service calls</li>
      <li><svg><use href="#tick-blue"/></svg>Annual Preventative Maintenance contracts</li>
    </ul>
    <p class="abs" style="left:13px;top:440px;width:210px;font-size:7.5px;line-height:11.5px">For a consultation for a whole home generator or one for your business, <b style="font-weight:600">contact us today at 479-555-0177</b></p>
  </div>

  <!-- Panel: telecom -->
  <div class="panel p3 white">
    <h2 class="abs serif-title" style="left:17px;top:22px;font-size:13.5px;font-weight:700">Telecommunications</h2>
    <ul class="abs ticks" style="left:17px;top:44px;width:205px;font-size:7.5px;line-height:10.6px">
      <li style="margin-bottom:3.5px"><svg><use href="#tick-blue"/></svg>Certified Fiber Optic Technicians</li>
      <li style="margin-bottom:3.5px"><svg><use href="#tick-blue"/></svg>With Over 30 Years Combined Experienced</li>
      <li style="margin-bottom:3.5px"><svg><use href="#tick-blue"/></svg>Experienced Installating both Single-mode and Muli-mode</li>
      <li style="margin-bottom:3.5px"><svg><use href="#tick-blue"/></svg>Emergency Fusion and Mechanical Splicing</li>
      <li style="margin-bottom:3.5px"><svg><use href="#tick-blue"/></svg>Data Networks Installation and troubleshooting</li>
      <li style="margin-bottom:3.5px"><svg><use href="#tick-blue"/></svg>Access Control</li>
      <li style="margin-bottom:3.5px"><svg><use href="#tick-blue"/></svg>Modifications and improvements</li>
      <li><svg><use href="#tick-blue"/></svg>Control Systems</li>
    </ul>
    <div class="abs trained">Sales, Service, Repair, Installation, Trained In Voltmax, Powerline, and Corvane.</div>
    <div class="photo" role="img" aria-label="Photo of workers beside a large switchgear unit at an outdoor site" style="left:0;top:244px;width:231px;height:232px;background:linear-gradient(180deg,#a9b8c8,#c7ccd2 40%,#8d949b 75%,#b49a78)"></div>
    <div class="abs" style="left:0;top:420px;width:120px;height:56px;background:rgba(255,255,255,.9)"></div>
    <div class="abs brand" style="left:7px;top:441px;font-size:7px"><i style="width:10px;height:10px"></i>BRIGHTLINE BUILDERS, INC.</div>
  </div>
  <div class="base-band"></div>
</section>

<div class="side-label" style="top:1115px">Side 2</div>

</body>
</html>
```